indépendant en tant que Massothérapeute et Préparateur Mental, j'ai besoin de ...

Massothérapeute et préparateur mental indépendant, je recherche une carte de visite sobre et dynamique, sans images liées au massage ou à la préparation mentale mais intégrant mon logo. Les couleurs que j'aime bien sont : Blanc, gris, anthracite, noir et jaune

Contact Information for Business Card

carte de préférence Horizontale
neutre qui puisse toucher le deux domaines Massothérapie et préparation mentale

Requirements
Must have
• mon projet doit intégrer au recto:
LOGO
Loïc Bardèze
078 513 26 48
info@loicbardeze.ch
et éventuellement www.loicbardeze.ch

et au verso les deux adresses:

Chemin des Ormilles 7B
1400 Yverdon-les-Bains

Route de la Gravière 9
1700 Fribourg

Should not have
• mon projet ne doit pas contenir d'image en liens avec le massage ni la préparation mentale.

```html
<!DOCTYPE html>
<html lang="fr">
<head>
<meta charset="UTF-8">
<title>Loïc Bardèze – Cartes de visite</title>
<link rel="stylesheet" href="https://fonts.googleapis.com/css2?family=Montserrat:wght@500;700&family=Roboto:wght@400&display=swap">
<style>
  :root {
    --bg: #1b1b1b;
    --card: #2c2c2c;
    --yellow: #f3bb12;
    --white: #f2f2f2;
    --grey: #cfcfcf;
  }
  * { box-sizing: border-box; margin: 0; padding: 0; }
  html, body {
    width: 1200px; height: 900px; overflow: hidden;
    background: var(--bg);
  }
  .canvas {
    width: 1200px; height: 900px;
    display: flex; flex-direction: column;
    align-items: center; justify-content: center; gap: 44px;
  }
  .card {
    position: relative;
    width: 600px; height: 388px;
    background: var(--card);
    box-shadow: 0 14px 34px rgba(0,0,0,.55);
    overflow: hidden;
  }
  .brand {
    position: absolute;
    display: flex; align-items: center; gap: 14px;
  }
  .brand-square {
    width: 26px; height: 26px; background: var(--yellow);
  }
  .brand-name {
    font-family: 'Montserrat', sans-serif; font-weight: 700;
    font-size: 34px; color: var(--yellow); letter-spacing: .5px;
  }
  .brand-tagline {
    position: absolute;
    font-family: 'Montserrat', sans-serif; font-weight: 500;
    font-size: 10.5px; letter-spacing: 1.6px; text-transform: uppercase;
    color: var(--yellow);
  }
  .divider {
    position: absolute; width: 2px; background: var(--yellow);
  }
  .address {
    position: absolute;
    font-family: 'Roboto', sans-serif; font-size: 15px; line-height: 1.4;
    color: var(--white);
  }

  /* back */
  .card--back .brand { left: 150px; top: 118px; }
  .card--back .brand-tagline { left: 190px; top: 166px; }
  .card--back .divider { left: 318px; top: 272px; height: 46px; }
  .card--back .address--yverdon { left: 70px; top: 272px; }
  .card--back .address--fribourg { left: 346px; top: 272px; }

  /* front */
  .card--front .brand { left: 150px; top: 100px; }
  .card--front .brand-tagline { left: 190px; top: 148px; }
  .person {
    position: absolute; left: 70px; top: 252px;
  }
  .person-name {
    font-family: 'Montserrat', sans-serif; font-weight: 700;
    font-size: 27px; color: var(--yellow);
  }
  .person-role {
    font-family: 'Montserrat', sans-serif; font-weight: 500;
    font-size: 15px; color: var(--white); text-align: right; margin-top: 2px;
  }
  .card--front .divider { left: 318px; top: 246px; height: 74px; }
  .contact-list {
    position: absolute; left: 342px; top: 244px;
    list-style: none;
    font-family: 'Roboto', sans-serif; font-size: 14.5px; color: var(--white);
  }
  .contact-list li {
    display: flex; align-items: center; gap: 10px; height: 26px;
  }
  .contact-icon { width: 15px; height: 15px; flex: none; }
</style>
</head>
<body>
<main class="canvas">

  <section class="card card--back" aria-label="Verso">
    <div class="brand">
      <span class="brand-square"></span>
      <span class="brand-name">Loïc Bardèze</span>
    </div>
    <p class="brand-tagline">Massothérapeute / Préparateur mental</p>

    <address class="address address--yverdon">Chemin des Ormilles 7B<br>1400 Yverdon-les-Bains</address>
    <span class="divider"></span>
    <address class="address address--fribourg">Route de la Gravière 9<br>1700 Freiburg</address>
  </section>

  <section class="card card--front" aria-label="Recto">
    <div class="brand">
      <span class="brand-square"></span>
      <span class="brand-name">Loïc Bardèze</span>
    </div>
    <p class="brand-tagline">Massothérapeute / Préparateur mental</p>

    <div class="person">
      <p class="person-name">Loïc Bardèze</p>
      <p class="person-role">Manager</p>
    </div>

    <span class="divider"></span>

    <ul class="contact-list">
      <li>
        <svg class="contact-icon" viewBox="0 0 24 24" aria-hidden="true">
          <path fill="#f3bb12" d="M6.6 10.8a15.1 15.1 0 0 0 6.6 6.6l2.2-2.2a1 1 0 0 1 1-.25 11.4 11.4 0 0 0 3.6.57 1 1 0 0 1 1 1V20a1 1 0 0 1-1 1A17 17 0 0 1 3 4a1 1 0 0 1 1-1h3.5a1 1 0 0 1 1 1c0 1.25.2 2.45.57 3.57a1 1 0 0 1-.25 1z"/>
        </svg>
        078 513 26 48
      </li>
      <li>
        <svg class="contact-icon" viewBox="0 0 24 24" aria-hidden="true">
          <rect x="2" y="5" width="20" height="14" rx="1.5" fill="#f3bb12"/>
          <path d="M3 6.5l9 6.5 9-6.5" fill="none" stroke="#2c2c2c" stroke-width="1.8"/>
        </svg>
        info@loicbardeze.ch
      </li>
      <li>
        <svg class="contact-icon" viewBox="0 0 24 24" aria-hidden="true">
          <g fill="none" stroke="#f3bb12" stroke-width="2">
            <circle cx="12" cy="12" r="9.5"/>
            <ellipse cx="12" cy="12" rx="4.2" ry="9.5"/>
            <path d="M2.5 12h19M4 7h16M4 17h16"/>
          </g>
        </svg>
        www.loicbardeze.ch
      </li>
    </ul>
  </section>

</main>
</body>
</html>
```